Meadowrun Acres Website Design

We have been redeveloping our website already and are quite happy with the content, but the design needs to be better:
https://tilvexa-hub.examplehost.net/

Pages, content, concept etc. Can all be taken from the redeveloped website.
The farmer can register and edit/view their profile, subscribe and these pages need to be designed better as well as contact, about, pricing, tos, privacy and a page with example portlets.

We need a website to appeal to farmers, investors and retiring farmers.

The design should be clean and a little country.

We don't want any repeat designs that some may submit to every project and has no respect for the project brief, so please don't submit them.

Target Market(s)

farmers, investors, retirees

Industry/Entity Type

Farming

Number of Pages Required

5+ page

Colors

Designer to choose colors to be used in the design.

Requirements
Must have
• Nice, clean modern design that is appealing
• Profile page laid out nicely

```html
<!DOCTYPE html>
<html lang="en">
<head>
<meta charset="utf-8">
<title>Meadowrun Acres</title>
<link href="https://fonts.googleapis.com/css2?family=Roboto:wght@300;400;500;700;900&display=swap" rel="stylesheet">
<style>
:root{
  --teal:#1d5e62;
  --teal-dark:#174b4f;
  --teal-title:#1f6a6d;
  --green:#5cb85c;
  --text:#555;
  --muted:#888;
  --line:#dcdcdc;
  --white:#fff;
}
*{box-sizing:border-box;margin:0;padding:0}
html,body{width:1200px;height:3756px;overflow:hidden}
body{font-family:"Roboto",Arial,sans-serif;color:var(--text);background:var(--white)}
.section-title{font-size:44px;font-weight:700;color:var(--teal-title);text-align:center;letter-spacing:.5px}

/* hero */
.hero{position:relative;height:600px;background:linear-gradient(180deg,#4d6b5d 0%,#6f8e6c 45%,#5a6a4e 75%,#3d4635 100%)}
.hero-photo{position:absolute;inset:0;background:radial-gradient(circle at 68% 42%,rgba(150,190,130,.55),transparent 30%),linear-gradient(180deg,rgba(29,94,98,.55),rgba(29,94,98,.25) 60%,rgba(30,35,25,.5))}
.nav{position:absolute;top:0;left:0;right:0;height:52px;background:rgba(23,75,79,.85);display:flex;align-items:center;padding:0 40px}
.brand{display:flex;align-items:center;gap:12px;color:var(--white);font-size:24px;font-weight:400}
.brand-dot{width:22px;height:22px;border-radius:50%;background:#a8d08d}
.nav-links{margin-left:auto;display:flex;gap:34px;list-style:none;color:var(--white);font-size:15px}
.nav-links li{display:flex;align-items:center;gap:7px}
.hero-title{position:absolute;top:258px;left:0;right:0;text-align:center;color:var(--white);font-size:46px;font-weight:700;letter-spacing:.5px}
.hero-actions{position:absolute;top:344px;left:0;right:0;display:flex;justify-content:center;gap:44px}
.btn-ghost{border:2px solid var(--white);color:var(--white);font-size:20px;font-weight:500;padding:14px 26px;width:250px;text-align:center;letter-spacing:.5px}
.hero-dots{position:absolute;bottom:28px;left:0;right:0;display:flex;justify-content:center;gap:10px}
.hero-dots span{width:10px;height:10px;border-radius:50%;background:rgba(255,255,255,.5)}
.hero-dots span:first-child{background:var(--white)}

/* own a farm */
.own{height:840px;padding-top:58px}
.intro{width:760px;margin:22px auto 0;text-align:center;font-size:14px;line-height:22px;color:var(--muted)}
.paths{display:flex;justify-content:center;gap:96px;margin-top:48px}
.path{width:180px;text-align:center;font-size:19px;font-weight:500;color:#444}
.path-icon{width:76px;height:76px;border-radius:50%;border:2px solid #9a9a9a;margin:0 auto 20px;display:flex;align-items:center;justify-content:center}
.video{position:relative;width:904px;height:404px;margin:56px auto 0;background:linear-gradient(135deg,#3a2d24,#6b5140 40%,#8a6a52 60%,#2d241d)}
.video-bar{position:absolute;top:0;left:0;right:0;height:40px;background:rgba(0,0,0,.55);color:#eee;font-size:16px;padding:11px 16px}
.video-play{position:absolute;left:50%;top:50%;width:72px;height:50px;margin:-25px 0 0 -36px;border-radius:12px;background:rgba(20,20,20,.8);display:flex;align-items:center;justify-content:center}
.video-controls{position:absolute;bottom:0;left:0;right:0;height:36px;background:rgba(0,0,0,.6)}
.video-progress{position:absolute;bottom:32px;left:10px;right:10px;height:3px;background:rgba(255,255,255,.35)}

/* bands */
.band{background:var(--teal);color:var(--white);text-align:center}
.band h2{font-size:30px;font-weight:700;padding-top:48px}
.band p{font-size:15px;margin-top:14px}
.band-actions{display:flex;justify-content:center;gap:26px;margin-top:22px}
.btn-line{border:2px solid var(--white);color:var(--white);font-size:17px;font-weight:500;padding:8px 0;width:230px;text-align:center;letter-spacing:.5px}
.band-member{height:192px}
.band-investor{height:196px}
.band-retire{height:192px}

/* aspiring */
.aspiring{height:620px;padding-top:64px}
.steps{display:flex;justify-content:center;gap:24px;margin-top:38px}
.step{width:300px;height:428px;border:1px solid var(--line);display:flex;flex-direction:column}
.step-head{background:var(--teal);color:var(--white);font-size:19px;text-align:center;padding:10px 0}
.step-art{height:222px;margin:30px 24px 0}
.step-art.family{background:linear-gradient(180deg,#fff,#e8e8e8 50%,#2a2a2a)}
.step-art.tractor{background:radial-gradient(circle at 50% 55%,#c0392b 0 22%,#7cb342 23% 40%,#fff 41%)}
.step-art.house{background:linear-gradient(180deg,#fff 30%,#2b2b2b 31% 80%,#fff 81%)}
.step-text{text-align:center;font-size:16px;color:#444;margin-top:24px;padding:0 30px;line-height:22px;height:60px}
.step-btn{margin:auto 16px 16px;background:var(--green);color:var(--white);font-size:14px;text-align:center;padding:7px 0}

/* testimonials */
.testimonials{height:440px;padding-top:50px}
.quotes{display:flex;justify-content:center;gap:26px;margin-top:38px}
.quote{width:310px;height:252px;border:1px solid var(--line);text-align:center;padding-top:20px}
.avatar{width:96px;height:96px;border-radius:50%;margin:0 auto;background:linear-gradient(160deg,#b58b6c,#6d4c3a)}
.avatar.alt{background:linear-gradient(160deg,#9aa3a8,#44505a)}
.quote h3{font-size:20px;font-weight:500;color:#333;margin-top:14px;padding-bottom:12px;border-bottom:1px solid var(--line)}
.quote p{font-size:12px;line-height:18px;color:var(--muted);padding:12px 22px 0}

/* blog */
.blog{height:584px;padding-top:52px}
.posts{display:flex;justify-content:center;gap:20px;margin-top:34px}
.post{position:relative;width:300px;height:440px}
.post.one{background:linear-gradient(180deg,#5b86a8,#8aa8b5 30%,#a1583d 60%,#5e3a2c)}
.post.two{background:linear-gradient(180deg,#b9c0c2,#8a9488 40%,#4d5a44)}
.post.three{background:linear-gradient(180deg,#6b2f4a,#2b1f26 60%,#8b1f35)}
.post-overlay{position:absolute;left:0;right:0;bottom:0;top:0;background:rgba(0,0,0,.3);color:var(--white);padding:214px 24px 0}
.post-overlay h3{font-size:26px;font-weight:500}
.post-overlay time{display:block;font-size:15px;margin-top:6px}
.post-overlay p{font-size:15px;line-height:20px;margin-top:8px}
.post-overlay span{display:block;font-size:15px;margin-top:6px}

/* footer */
.footer{height:92px;background:var(--teal-dark);color:#cfdede;text-align:center;padding-top:20px}
.social{display:flex;justify-content:center;gap:10px}
.social span{width:24px;height:24px;border-radius:50%;border:1px solid #cfdede}
.footer p{font-size:12px;margin-top:12px}
</style>
</head>
<body>

<header class="hero">
  <div class="hero-photo" role="img" aria-label="Close-up of hands cupping soil with a young green seedling"></div>
  <nav class="nav">
    <div class="brand"><span class="brand-dot"></span>Meadowrun Acres</div>
    <ul class="nav-links">
      <li>Home</li>
      <li>Aspiring Farmers</li>
      <li>Investors</li>
      <li>Retiring Farmer</li>
      <li>Blog Pricing</li>
      <li><svg width="14" height="14" viewBox="0 0 14 14"><circle cx="7" cy="4" r="3" fill="#fff"/><path d="M1 14c0-4 3-6 6-6s6 2 6 6z" fill="#fff"/></svg>Login</li>
    </ul>
  </nav>
  <h1 class="hero-title">IT'S TIME TO REALISE YOUR FARMING DREAM</h1>
  <div class="hero-actions">
    <div class="btn-ghost">SIGN UP NOW &nbsp;→</div>
    <div class="btn-ghost">READ MORE &nbsp;▸</div>
  </div>
  <div class="hero-dots"><span></span><span></span></div>
</header>

<section class="own">
  <h2 class="section-title">YOU CAN OWN A FARM</h2>
  <p class="intro">We know how hard it is for a young family to find the capital needed to own and operate their own farm. So we started Meadowrun Acres. We want to rejuvenate regional farming by putting land back in the hands of people who love it.</p>
  <div class="paths">
    <div class="path"><div class="path-icon"><svg width="36" height="36" viewBox="0 0 36 36" fill="none" stroke="#777" stroke-width="2"><circle cx="13" cy="11" r="5"/><circle cx="25" cy="13" r="4"/><path d="M4 30c0-6 4-10 9-10s9 4 9 10M22 30c0-5 2-8 6-8s5 3 5 8"/></svg></div>Connect A Young</div>
    <div class="path"><div class="path-icon"><svg width="36" height="36" viewBox="0 0 36 36" fill="none" stroke="#777" stroke-width="2"><path d="M6 26h24M10 26V14h16v12M14 14V9h8v5"/><circle cx="12" cy="29" r="3"/><circle cx="26" cy="29" r="3"/></svg></div>Retiring Farming</div>
    <div class="path"><div class="path-icon"><svg width="36" height="36" viewBox="0 0 36 36" fill="none" stroke="#777" stroke-width="2"><rect x="11" y="5" width="14" height="26" rx="2"/><path d="M18 11v12M15 14h5a2 2 0 010 4h-4a2 2 0 000 4h5"/></svg></div>Investors</div>
    <div class="path"><div class="path-icon"><svg width="36" height="36" viewBox="0 0 36 36" fill="none" stroke="#777" stroke-width="2"><path d="M4 16l8-6 6 4 6-4 8 6-10 9-4-3-4 3z"/></svg></div>Operate Farm Together</div>
  </div>
  <div class="video" role="img" aria-label="Video still of a presenter talking in a warmly lit living room">
    <div class="video-bar">What is Meadowrun Acres About</div>
    <div class="video-play"><svg width="22" height="24" viewBox="0 0 22 24"><path d="M2 2l18 10-18 10z" fill="#fff"/></svg></div>
    <div class="video-progress"></div>
    <div class="video-controls"></div>
  </div>
</section>

<section class="band band-member">
  <h2>Subscribe to be Either an Aspiring or Premium Farmer to Receive</h2>
  <p>Free Fieldline market analysis membership (valued at $300 pa). Visit our pricing page to find out more.</p>
  <div class="band-actions"><div class="btn-line">JOIN US NOW</div></div>
</section>

<section class="aspiring">
  <h2 class="section-title">Aspiring Farmers</h2>
  <div class="steps">
    <article class="step">
      <div class="step-head">Step 1</div>
      <div class="step-art family" role="img" aria-label="Silhouette of a young family"></div>
      <p class="step-text">Register as an Aspiring Farmer</p>
      <div class="step-btn">Register</div>
    </article>
    <article class="step">
      <div class="step-head">Step 2</div>
      <div class="step-art tractor" role="img" aria-label="Illustration of a farmer on a red tractor surrounded by crops"></div>
      <p class="step-text">Build your farm skills to get yourself farm-ready</p>
      <div class="step-btn">Farm ready</div>
    </article>
    <article class="step">
      <div class="step-head">Step 3</div>
      <div class="step-art house" role="img" aria-label="Silhouette of a farmhouse with trees"></div>
      <p class="step-text">Together we find you your dream farm</p>
      <div class="step-btn">Match making</div>
    </article>
  </div>
</section>

<section class="band band-investor">
  <h2>Subscribe To Be An Investors</h2>
  <p>We have the best farmers in Australia ready to work with you on your farm</p>
  <div class="band-actions"><div class="btn-line">JOIN US NOW</div><div class="btn-line">FIND OUT MORE</div></div>
</section>

<section class="testimonials">
  <h2 class="section-title">Testimonials</h2>
  <div class="quotes">
    <article class="quote">
      <div class="avatar" role="img" aria-label="Portrait photo of Tessa Marlow"></div>
      <h3>Tessa Marlow</h3>
      <p>Working with this team was a bright start for growing new farmers, and we are proud to have helped with the growth of young families on the land.</p>
    </article>
    <article class="quote">
      <div class="avatar alt" role="img" aria-label="Portrait photo of Hugh Brenton"></div>
      <h3>Hugh Brenton</h3>
      <p>Meadowrun Acres has offered us a real way to pass our property to people with the skills and ambition to keep our family farming legacy alive.</p>
    </article>
    <article class="quote">
      <div class="avatar alt" role="img" aria-label="Portrait photo of Elliot Varga"></div>
      <h3>Elliot Varga</h3>
      <p>I was won over by the idea that investors could back the people who make the land work, and the results have been strong for our small fund.</p>
    </article>
  </div>
</section>

<section class="band band-retire">
  <h2>Subscribe To Be Retiring Farmers</h2>
  <p>Are you looking for a positive way to step back from your farm? Get in touch discuss the best farm succession opportunity for you</p>
  <div class="band-actions"><div class="btn-line">ENQUIRE NOW</div><div class="btn-line">FIND OUT MORE</div></div>
</section>

<section class="blog">
  <h2 class="section-title">Our Blog</h2>
  <div class="posts">
    <div class="post one" role="img" aria-label="Photo of two farmers in hats outdoors"></div>
    <div class="post two" role="img" aria-label="Photo of a country scene">
      <div class="post-overlay">
        <h3>Meadowrun Acres TV</h3>
        <time>12 April 2017</time>
        <p>New episode: another couple begins their journey with Meadowrun Acres</p>
        <span>Read More</span>
      </div>
    </div>
    <div class="post three" role="img" aria-label="Portrait photo of a businesswoman"></div>
  </div>
</section>

<footer class="footer">
  <div class="social"><span></span><span></span><span></span><span></span></div>
  <p>© Meadowrun Acres 2017. All Rights Reserved</p>
</footer>

</body>
</html>
```